Business card design for Automotive workshop

We need a business card for a new automotive repair and tyre shop called Keelstone Prime Automotive located in New Zealand. We are a clean, modern and fresh workshop and company.

Front needs to feature logo,
my name:
Marlo Fenwicke (director)

Address:
48 Tarn Lane
Whitianga 3510

Phone: 07 594 2713
Mobile: 027 451 9362
Email: office@keelstoneautomotive.example.nz
Website: keelstoneautomotive.example.nz

Back needs to feature an area to write down appointment details, date and time.

Also feature a list of jobs and work we do such as,
Vehicle Servicing
All Mechanical Repairs
Warrant of Fitness
Tyres & Wheel Alignments
Automotive Diagnostics
Automotive Parts & Supplies

```html
<!DOCTYPE html>
<html lang="en">
<head>
<meta charset="utf-8">
<title>Keelstone Prime Automotive – Business Card</title>
<link rel="stylesheet" href="https://fonts.googleapis.com/css2?family=Arimo:wght@400;700&display=swap">
<style>
  :root {
    --bg: #3b3431;
    --card-black: #0b0b0b;
    --card-white: #ffffff;
    --red: #e3262d;
    --faint-dark: #1c1c1c;
    --faint-light: #eeeae8;
  }
  * { box-sizing: border-box; margin: 0; padding: 0; }
  html, body { width: 1200px; height: 768px; overflow: hidden; }
  body {
    background: var(--bg);
    font-family: "Arimo", Arial, sans-serif;
    position: relative;
  }
  .card {
    position: absolute;
    top: 234px;
    width: 520px;
    height: 300px;
    background: var(--card-black);
    overflow: hidden;
    box-shadow: 0 10px 24px rgba(0,0,0,0.45);
  }
  .card--back { left: 50px; }
  .card--front { left: 630px; }

  .brand {
    position: absolute;
    color: var(--red);
    font-weight: 700;
    font-size: 19px;
    letter-spacing: 0.5px;
    white-space: nowrap;
    display: flex;
    align-items: center;
    gap: 8px;
  }
  .brand__dot {
    width: 12px; height: 12px; border-radius: 50%;
    background: var(--red);
    display: inline-block;
  }

  /* back */
  .card--back .vehicle-art {
    position: absolute;
    left: 110px; top: 30px;
    width: 330px; height: 200px;
    border-radius: 90px 120px 60px 60px;
    background: radial-gradient(ellipse at center, #262626 0%, #161616 60%, rgba(11,11,11,0) 100%);
  }
  .card--back .brand { left: 200px; top: 48px; }
  .services {
    position: absolute;
    list-style: none;
    color: var(--red);
    font-size: 13px;
    line-height: 19px;
  }
  .services li { display: flex; align-items: center; gap: 8px; }
  .services li::before {
    content: ""; width: 8px; height: 8px; border-radius: 50%;
    background: var(--red); flex: none;
  }
  .services--left { left: 26px; top: 30px; }
  .services--right { left: 246px; top: 116px; }
  .appointment-label {
    position: absolute;
    color: var(--red);
    font-size: 13px;
  }
  .appointment-field {
    position: absolute;
    background: var(--card-white);
    border-radius: 14px;
    height: 32px;
  }
  .label-date { left: 22px; top: 96px; }
  .field-date { left: 62px; top: 104px; width: 168px; }
  .label-time { left: 232px; top: 190px; }
  .field-time { left: 280px; top: 200px; width: 200px; }

  /* front */
  .card--front .band-white {
    position: absolute;
    left: 0; top: 110px;
    width: 520px; height: 128px;
    background: var(--card-white);
  }
  .card--front .vehicle-art {
    position: absolute;
    left: 70px; top: 100px;
    width: 300px; height: 180px;
    border-radius: 80px 110px 50px 50px;
    background: radial-gradient(ellipse at center, var(--faint-light) 0%, rgba(238,234,232,0.4) 60%, rgba(238,234,232,0) 100%);
  }
  .card--front .brand { left: 40px; top: 48px; }
  .phones, .contacts {
    position: absolute;
    list-style: none;
    color: var(--red);
    font-size: 13px;
    line-height: 20px;
  }
  .phones { left: 30px; top: 128px; }
  .contacts { left: 240px; top: 178px; }
  .phones li, .contacts li { display: flex; align-items: center; gap: 7px; white-space: nowrap; }
  .icon { width: 12px; height: 12px; flex: none; }
  .person {
    position: absolute;
    left: 300px; top: 118px;
    color: var(--red);
  }
  .person__name {
    font-size: 20px; font-weight: 700;
    display: flex; align-items: center; gap: 7px;
  }
  .person__role { font-size: 15px; margin-left: 6px; margin-top: 2px; }
</style>
</head>
<body>

<section class="card card--back" aria-label="Card back">
  <div class="vehicle-art" role="img" aria-label="Faint vehicle illustration"></div>
  <div class="brand"><span class="brand__dot"></span>Keelstone Prime Automotive</div>
  <ul class="services services--left">
    <li>Vehicle Servicing</li>
    <li>All Mechanical Repairs</li>
    <li>Warrant of Fitness</li>
  </ul>
  <ul class="services services--right">
    <li>Tyres &amp; Wheel Alignments</li>
    <li>Automotive Parts &amp; Supplies</li>
    <li>Automotive Diagnostics</li>
  </ul>
  <span class="appointment-label label-date">Date</span>
  <div class="appointment-field field-date"></div>
  <span class="appointment-label label-time">Time</span>
  <div class="appointment-field field-time"></div>
</section>

<section class="card card--front" aria-label="Card front">
  <div class="band-white"></div>
  <div class="vehicle-art" role="img" aria-label="Faint vehicle illustration"></div>
  <div class="brand"><span class="brand__dot"></span>Keelstone Prime Automotive</div>

  <ul class="phones">
    <li>
      <svg class="icon" viewBox="0 0 12 12"><circle cx="6" cy="6" r="6" fill="#e3262d"/><path d="M4 3l1.2 1.4-.6.8c.4.9 1 1.5 1.9 1.9l.8-.6L8.7 8 8 9C5.5 8.7 3.3 6.5 3 4z" fill="#fff"/></svg>
      027 451 9362
    </li>
    <li>
      <svg class="icon" viewBox="0 0 12 12"><circle cx="6" cy="6" r="6" fill="#e3262d"/><rect x="3" y="5" width="6" height="4" rx="1" fill="#fff"/><rect x="3.5" y="3" width="5" height="1.5" rx="0.7" fill="#fff"/></svg>
      07 594 2713
    </li>
  </ul>

  <div class="person">
    <div class="person__name">
      <svg class="icon" viewBox="0 0 12 12"><circle cx="6" cy="6" r="6" fill="#e3262d"/><circle cx="6" cy="4.3" r="1.8" fill="#fff"/><path d="M2.8 9.5c.5-1.8 1.7-2.6 3.2-2.6s2.7.8 3.2 2.6z" fill="#fff"/></svg>
      Marlo Fenwicke
    </div>
    <div class="person__role">(Managing director)</div>
  </div>

  <ul class="contacts">
    <li>
      <svg class="icon" viewBox="0 0 12 12"><circle cx="6" cy="6" r="6" fill="#e3262d"/><rect x="3" y="4" width="6" height="4.2" fill="#fff"/><path d="M3 4l3 2.4L9 4" stroke="#e3262d" stroke-width="0.8" fill="none"/></svg>
      office@keelstoneautomotive.example.nz
    </li>
    <li>
      <svg class="icon" viewBox="0 0 12 12"><circle cx="6" cy="6" r="6" fill="#e3262d"/><circle cx="6" cy="6" r="3.2" fill="none" stroke="#fff" stroke-width="0.9"/><path d="M2.8 6h6.4M6 2.8c-1.5 1.8-1.5 4.6 0 6.4M6 2.8c1.5 1.8 1.5 4.6 0 6.4" stroke="#fff" stroke-width="0.7" fill="none"/></svg>
      keelstoneautomotive.example.nz
    </li>
    <li>
      <svg class="icon" viewBox="0 0 12 12"><circle cx="6" cy="6" r="6" fill="#e3262d"/><path d="M2.8 6.2L6 3.2l3.2 3h-.9v2.6H3.7V6.2z" fill="#fff"/></svg>
      48 Tarn Lane Whitianga 3510
    </li>
  </ul>
</section>

</body>
</html>
```